Modern card design needed for building development company

We are looking for a sharp modern new look for our business cards.
We are a New Zealand based company called TKR Ventures NZ LTD that specialises in subdividing large sections, housing and commercial buildings.
We have attached a photo of the current logo and would like to see it improved somehow as it looks a bit dated.
We are open to any colours.

Target Market(s)

Investors, Property buyers

Industry/Entity Type

Investment

Contact Information for Business Card

TKR VENTURES NZ LTD
www.tkrventuresnz.co.nz

Damon Whitcombe
Phone +64 21 938 104
Email dpwhitcombe@korumail.co.nz

Font styles to use
Serif
Sans Serif

Colors
0792cd
33a6d7
85cae6
6b449b
886aae
f04a50
ec1f27
f37122
f68d4d

Requirements
Must have
• Please try and make the logo more modern or if you have a similar one we would like to see it.

```html
<!DOCTYPE html>
<html lang="en">
<head>
<meta charset="utf-8">
<title>TKR Ventures NZ LTD – Business Card</title>
<link rel="stylesheet" href="https://fonts.googleapis.com/css2?family=Cinzel:wght@500&family=Roboto:wght@400;500&display=swap">
<style>
  :root {
    --brand-red: #961a28;
    --ink-grey: #555555;
    --card-white: #ffffff;
    --backdrop: #e6e6e6;
    --serif: "Cinzel", Georgia, serif;
    --sans: "Roboto", Arial, sans-serif;
  }
  * { box-sizing: border-box; margin: 0; padding: 0; }
  html, body { width: 1200px; height: 1000px; overflow: hidden; }
  body { background: var(--backdrop); position: relative; font-family: var(--sans); }

  .card {
    position: absolute;
    left: 307px;
    width: 588px;
    height: 335px;
    box-shadow: 0 2px 6px rgba(0,0,0,0.18);
    overflow: hidden;
  }
  .card--front { top: 135px; background: var(--card-white); }
  .card--back { top: 523px; background: var(--brand-red); }

  .wordmark {
    position: absolute;
    display: flex;
    align-items: center;
    gap: 10px;
    font-family: var(--serif);
    font-weight: 500;
    white-space: nowrap;
  }
  .wordmark__square { display: block; flex: none; background: currentColor; }

  .card--front .wordmark {
    left: 26px; top: 150px;
    font-size: 17px; color: var(--brand-red);
  }
  .card--front .wordmark__square { width: 12px; height: 12px; }

  .divider {
    position: absolute;
    left: 276px; top: 102px;
    width: 2px; height: 128px;
    background: var(--brand-red);
  }

  .contact { position: absolute; left: 300px; top: 140px; }
  .contact__name {
    font-size: 22px; font-weight: 500;
    color: var(--brand-red); letter-spacing: 0.3px;
    margin-bottom: 10px;
  }
  .contact__line {
    display: flex; align-items: center; gap: 10px;
    font-size: 14px; color: var(--ink-grey);
    line-height: 20px;
  }
  .contact__icon { width: 10px; height: 10px; flex: none; }

  .web-band {
    position: absolute;
    right: 0; bottom: 0;
    width: 290px; height: 26px;
    background: var(--brand-red);
    clip-path: polygon(22px 0, 100% 0, 100% 100%, 0 100%);
    color: var(--card-white);
    font-size: 13px;
    display: flex; align-items: center; justify-content: flex-end;
    padding-right: 18px;
  }

  .card--back .wordmark {
    left: 0; right: 0; top: 150px;
    justify-content: center;
    font-size: 28px; color: var(--card-white);
    gap: 14px;
  }
  .card--back .wordmark__square { width: 18px; height: 18px; }
</style>
</head>
<body>

  <section class="card card--front" aria-label="Business card front">
    <div class="wordmark">
      <span class="wordmark__square"></span>
      <span class="wordmark__name">TKR VENTURES NZ LTD</span>
    </div>

    <div class="divider"></div>

    <div class="contact">
      <p class="contact__name">DAMON WHITCOMBE</p>
      <p class="contact__line">
        <svg class="contact__icon" viewBox="0 0 10 10" aria-hidden="true">
          <path d="M2 0.5 L3.6 0.5 L4.2 3 L3 3.8 Q4 6 6.2 7 L7 5.8 L9.5 6.4 L9.5 8 Q9.5 9.5 8 9.5 Q0.5 9 0.5 2 Q0.5 0.5 2 0.5 Z" fill="#961a28"/>
        </svg>
        +64 21 938 104
      </p>
      <p class="contact__line">
        <svg class="contact__icon" viewBox="0 0 10 10" aria-hidden="true">
          <rect x="0.5" y="1.5" width="9" height="7" fill="none" stroke="#961a28" stroke-width="1.2"/>
          <path d="M0.8 2 L5 5.3 L9.2 2" fill="none" stroke="#961a28" stroke-width="1.2"/>
        </svg>
        dpwhitcombe@korumail.co.nz
      </p>
    </div>

    <div class="web-band">www.tkrventuresnz.co.nz</div>
  </section>

  <section class="card card--back" aria-label="Business card back">
    <div class="wordmark">
      <span class="wordmark__square"></span>
      <span class="wordmark__name">TKR VENTURES NZ LTD</span>
    </div>
  </section>

</body>
</html>
```